Telecommunications/Power civil contractor needs business card design

Were a new telecommunications/power underground civil contractor that is looking for a new business card design. Our company colours are silver or grey and orange. Feel free to use the white background logo or the black background logo.

Target Market(s)

Local contractors, utility companies, private sector mining/energy companies, developers.

Industry/Entity Type

Telecommunications

Contact Information for Business Card

Each card will need the following info:
Persons name:
Title:
E-mail:
Phone number:
Shop Address:
Mailing Address:

Requirements
Must have
• Each card will need the following info:
• Persons name:
• Title:
• E-mail:
• Phone number:
• Shop Address:
• Mailing Address:

```html
<!DOCTYPE html>
<html lang="en">
<head>
<meta charset="utf-8">
<title>Ridgeline Civil Contracting – Business Card</title>
<link href="https://fonts.googleapis.com/css2?family=Open+Sans:wght@400;600;700;800&display=swap" rel="stylesheet">
<style>
  :root {
    --orange: #f15a24;
    --grey: #8c8c8c;
    --grey-light: #bdbdbd;
    --grey-dark: #555555;
    --white: #ffffff;
    --black: #141414;
    --backdrop: #e9e6e1;
  }
  * { box-sizing: border-box; margin: 0; padding: 0; }
  html, body {
    width: 1200px; height: 935px; overflow: hidden;
    background: var(--backdrop);
    font-family: "Open Sans", Arial, sans-serif;
  }
  .canvas {
    width: 1200px; height: 935px;
    display: flex; align-items: center; justify-content: center; gap: 50px;
  }
  .card {
    position: relative;
    width: 540px; height: 309px;
    overflow: hidden;
    box-shadow: 0 6px 18px rgba(0,0,0,.18);
  }
  /* Front */
  .card-front { background: var(--white); }
  .card-front .wave { position: absolute; inset: 0; width: 100%; height: 100%; z-index: 0; }
  .brand {
    position: absolute; left: 26px; top: 22px; z-index: 1;
    display: flex; align-items: center; gap: 12px;
  }
  .brand-dot {
    width: 46px; height: 46px; border-radius: 50%;
    background: var(--orange);
  }
  .brand-name {
    color: var(--orange);
    font-weight: 800; font-size: 22px; line-height: 1.05;
    letter-spacing: .5px; text-transform: uppercase;
  }
  .person {
    position: absolute; right: 28px; top: 82px; text-align: right; z-index: 1;
  }
  .person-name { color: var(--orange); font-weight: 700; font-size: 17px; line-height: 1.3; }
  .person-title { color: var(--grey-dark); font-size: 15px; line-height: 1.3; }
  .contact {
    position: absolute; right: 24px; bottom: 16px; z-index: 1;
    color: var(--white); font-size: 13px; line-height: 19px; text-align: right;
    list-style: none;
  }
  .contact li { display: flex; justify-content: flex-end; align-items: center; gap: 6px; }
  .contact .icon { width: 13px; height: 13px; flex: none; }
  /* Back */
  .card-back {
    background: var(--black);
    display: flex; align-items: center; justify-content: center; gap: 14px;
  }
  .back-dot {
    width: 64px; height: 64px; border-radius: 50%;
    background: var(--orange);
  }
  .back-name {
    color: var(--orange);
    font-weight: 800; font-size: 26px; line-height: 1.05;
    letter-spacing: .5px; text-transform: uppercase;
  }
</style>
</head>
<body>
<main class="canvas">
  <section class="card card-front" aria-label="Business card front">
    <svg class="wave" viewBox="0 0 540 309" preserveAspectRatio="none" aria-hidden="true">
      <path d="M0 95 C150 115 300 150 540 150 L540 157 C300 157 150 124 0 109 Z" fill="var(--grey-light)"/>
      <path d="M0 118 C150 140 300 162 540 162 L540 168 C300 168 150 150 0 131 Z" fill="var(--grey)"/>
      <path d="M0 142 C150 166 300 176 540 176 L540 309 L0 309 Z" fill="var(--orange)"/>
      <path d="M0 153 C150 176 300 184 540 184" fill="none" stroke="var(--white)" stroke-width="2"/>
    </svg>

    <div class="brand">
      <span class="brand-dot"></span>
      <span class="brand-name">Ridgeline Civil<br>Contracting Inc</span>
    </div>

    <div class="person">
      <p class="person-name">Dalton Reyes</p>
      <p class="person-title">Managing Director</p>
    </div>

    <ul class="contact">
      <li>N. 48 Ember Road,</li>
      <li>Suite 210, Spokane,</li>
      <li>WA 55501</li>
      <li>555.010.2048
        <svg class="icon" viewBox="0 0 16 16" aria-hidden="true"><circle cx="8" cy="8" r="8" fill="var(--white)"/><path d="M5 4h2l1 2.5-1.2 1a5 5 0 0 0 2.7 2.7l1-1.2L13 10v2a1 1 0 0 1-1 1A8 8 0 0 1 4 5a1 1 0 0 1 1-1z" fill="var(--orange)"/></svg>
      </li>
      <li>info@ridgelinecivil.com
        <svg class="icon" viewBox="0 0 16 16" aria-hidden="true"><circle cx="8" cy="8" r="8" fill="var(--white)"/><rect x="4" y="5" width="8" height="6" fill="var(--orange)"/><path d="M4 5l4 3.5L12 5" fill="none" stroke="var(--white)" stroke-width="1"/></svg>
      </li>
    </ul>
  </section>

  <section class="card card-back" aria-label="Business card back">
    <span class="back-dot"></span>
    <span class="back-name">Ridgeline Civil<br>Contracting Inc</span>
  </section>
</main>
</body>
</html>
```